Blog Banner Design Project: Wanderly Ledger

Looking for a new banner for my blog " Neville Ostrander's Wanderly Ledger" at http://www.wanderlyledger.net - and once design agreed also want an updated album art for the podcast that goes along with the site.
For more about the blog and what it is about:
http://www.wanderlyledger.net/about
Wanderly Ledger is a Luxury Travel Blog And Podcast that provides inspiration, advice and tips about luxurious travel experiences, including destinations, transportation, accommodation, and journeys, that travellers can read, listen to or watch.
Objective of the new design
(1) retain the colour scheme ideally to retain the brand identity, as have been using these colours since 2005.
(2) introduce more of my personality and make it more visually and overt that it is "Neville Ostrander's Wanderly Ledger", so possibly introducing my image into the blog banner so visitors are clear and more aware of the person behind the brand.
(3) needs to have an up-market, luxury but modern feel.
(4) if possible reflect the focus on the content (destinations, transportation, accommodation, attractions and journeys) - but this maybe best left to just words as want the design to be bold and more of the branding and personality.
Ideal wording
Smallish: Neville Ostrander's
Main wording: Wanderly Ledger
Sub-title/ small: luxurious destinations, transportation, accommodation and journeys.
I have a poll running with readers of my blog to rate the designs to help me to chose the final route, and so there is no need to submit any more designs. I will make the decision once the poll closes on the weekend.

```html
<!DOCTYPE html>
<html lang="en">
<head>
<meta charset="utf-8">
<title>Neville Ostrander's Wanderly Ledger</title>
<link rel="stylesheet" href="https://fonts.googleapis.com/css2?family=Dancing+Script:wght@500&family=Gelasio:wght@400;700&display=swap">
<style>
  :root {
    --ink: #000000;
    --white: #ffffff;
    --tag-purple: #9a2b90;
    --beach-light: #d9cdb8;
    --beach-sky: #aebfcc;
    --falls-green: #5c6a3e;
    --falls-rock: #6b5a45;
    --coast-sky: #9fc3dc;
    --coast-sea: #5f8aa8;
    --paris-sky: #c9cccf;
    --paris-lawn: #7c8a5a;
    --night-sky: #4a4440;
    --night-city: #1f1c1a;
    --map-paper: #e6dcc4;
    --map-edge: #cfc1a2;
    --portrait-warm: #c49a82;
    --portrait-dark: #2f3440;
  }
  html, body {
    margin: 0;
    padding: 0;
    overflow: hidden;
    background: var(--white);
  }
  .banner {
    position: relative;
    width: 1200px;
    height: 202px;
    overflow: hidden;
    background: var(--beach-sky);
  }
  .scene {
    position: absolute;
    top: 0;
    height: 202px;
  }
  .scene--beach { left: 0; width: 300px; background: linear-gradient(180deg, var(--beach-sky) 0%, var(--beach-light) 55%, #c8b89a 100%); }
  .scene--falls { left: 260px; width: 170px; background: linear-gradient(180deg, var(--falls-green) 0%, var(--falls-rock) 60%, #8a9a70 100%); }
  .scene--coast { left: 417px; width: 190px; background: linear-gradient(180deg, var(--coast-sky) 0%, #c7dbe8 45%, var(--coast-sea) 100%); }
  .scene--paris { left: 594px; width: 220px; background: linear-gradient(180deg, var(--paris-sky) 0%, #b9bcbe 60%, var(--paris-lawn) 100%); }
  .scene--night { left: 808px; width: 235px; background: linear-gradient(180deg, var(--night-sky) 0%, #6a5e52 45%, var(--night-city) 100%); }
  .scene--map { left: 1036px; width: 164px; background: linear-gradient(90deg, var(--map-edge) 0%, var(--map-paper) 40%, #efe7d3 100%); }
  .portrait {
    position: absolute;
    left: 0;
    top: 0;
    width: 260px;
    height: 202px;
    background: radial-gradient(ellipse 45% 40% at 48% 35%, var(--portrait-warm) 0%, rgba(196,154,130,0.6) 60%, rgba(196,154,130,0) 100%),
                linear-gradient(180deg, rgba(0,0,0,0) 55%, var(--portrait-dark) 100%);
  }
  .title-band {
    position: absolute;
    left: 0;
    top: 0;
  }
  .byline {
    position: absolute;
    left: 292px;
    top: 23px;
    font-family: "Dancing Script", cursive;
    font-weight: 500;
    font-size: 33px;
    line-height: 38px;
    color: var(--white);
    margin: 0;
  }
  .blog-name {
    position: absolute;
    left: 376px;
    top: 64px;
    margin: 0;
    font-family: "Gelasio", Georgia, serif;
    font-weight: 400;
    font-size: 64px;
    line-height: 72px;
    color: var(--white);
    letter-spacing: 0.2px;
  }
  .tagline {
    position: absolute;
    left: 430px;
    top: 169px;
    margin: 0;
    font-family: "Gelasio", Georgia, serif;
    font-weight: 700;
    font-size: 19.5px;
    line-height: 33px;
    color: var(--white);
    white-space: nowrap;
  }
</style>
</head>
<body>
<header class="banner">
  <div class="scene scene--beach" role="img" aria-label="Photo of a sunny beach with sunbathers"></div>
  <div class="scene scene--falls" role="img" aria-label="Photo of a waterfall among green cliffs"></div>
  <div class="scene scene--coast" role="img" aria-label="Photo of a coastal highway beside the sea"></div>
  <div class="scene scene--paris" role="img" aria-label="Photo of the Paris skyline with the iron tower"></div>
  <div class="scene scene--night" role="img" aria-label="Photo of a city skyline at dusk"></div>
  <div class="scene scene--map" role="img" aria-label="Old paper map"></div>
  <div class="portrait" role="img" aria-label="Portrait of Neville Ostrander smiling"></div>

  <svg class="title-band" width="1200" height="202" viewBox="0 0 1200 202" aria-hidden="true">
    <defs>
      <linearGradient id="bandFade" x1="0" x2="1" y1="0" y2="0">
        <stop offset="0" stop-color="#000" stop-opacity="0.85"/>
        <stop offset="0.85" stop-color="#000" stop-opacity="0.85"/>
        <stop offset="1" stop-color="#000" stop-opacity="0"/>
      </linearGradient>
    </defs>
    <rect x="335" y="57" width="690" height="88" fill="url(#bandFade)"/>
    <polygon points="288,23 578,23 572,61 280,61" fill="var(--tag-purple)"/>
    <rect x="417" y="168" width="783" height="34" fill="var(--ink)" fill-opacity="0.9"/>
  </svg>

  <p class="byline">Neville Ostrander's</p>
  <h1 class="blog-name">Wanderly Ledger</h1>
  <p class="tagline">Luxurious destinations, transportation, accommodation and journeys.</p>
</header>
</body>
</html>
```